Celvara Health Group Presentation Folder, for Cancer Awareness, VERY COLORFUL AND MODERN

Presentation Folder I know pretty much what i want so it should be very eazy , I have included files from folders I use now rebrand them to my new company they will be fine, no sense re creating the wheel
Full Bleed Size
20.87" x 16.68"
53 x 42.4 cm
6260 x 5004 pixels
Document Trim Size
20.75" x 16.56"
52.7 x 42.1 cm
6225 x 4969 pixels

Low design quality

Industry/Entity Type

Medical

Font styles to use
Serif

Colors

Designer to choose colors to be used in the design.

Requirements
Must have
• really I am not looking for some one to redesign, we like our folder front page and would like to see new word information added., there are two folder front pages to choose from
• So Keep the original front page and redesign the back page and the pockets
• Can Make your Design off of one of the ones I already uploaded
Nice to have
• Keep the same color schemes, Keep the original front page and redesign the back page and the pockets
Should not have
• DO not recreate the front covers, use what I gave you and just rebrand

```html
<!DOCTYPE html>
<html lang="en">
<head>
<meta charset="utf-8">
<title>Celvara Health Group – Hereditary Cancer Screening Folder</title>
<link href="https://fonts.googleapis.com/css2?family=Raleway:wght@300;400;500;700;800&family=Rubik:wght@700&display=swap" rel="stylesheet">
<style>
  :root{
    --backdrop:#8a8a8a;
    --paper:#ffffff;
    --navy:#1b2a6b;
    --green:#8dc63f;
    --pink:#f29aab;
    --slate:#6d6e71;
    --ink:#222222;
    --grey-text:#555a60;
    --safe:#7fd3ea;
    --die:#e0393e;
    --fold:#7cc08a;
  }
  *{box-sizing:border-box;margin:0;padding:0}
  html,body{width:1096px;height:1200px;overflow:hidden}
  body{background:radial-gradient(ellipse at center,#9a9a9a 0%,var(--backdrop) 100%);font-family:"Raleway",sans-serif;position:relative}
  .dieline{position:absolute;left:0;top:0;width:1096px;height:1200px}
  .abs{position:absolute}

  /* cover panels */
  .photo{position:absolute;box-shadow:2px 4px 8px rgba(0,0,0,.35);border:4px solid #fff}
  .photo--beach{left:122px;top:190px;width:392px;height:222px;transform:rotate(-5deg);
    background:linear-gradient(180deg,#2f8fe0 0%,#6cc0f0 45%,#f4f4ee 58%,#e6dcc8 100%)}
  .photo--table{left:597px;top:258px;width:376px;height:232px;transform:rotate(-4deg);
    background:linear-gradient(160deg,#f3f0ea 0%,#d9c2a5 45%,#b79773 100%)}
  .ribbon{position:absolute;width:16px;height:62px;border-radius:8px;
    background:linear-gradient(180deg,#5aaee8 0%,#c45ad6 55%,#f07ab8 100%)}
  .ribbon--left{left:468px;top:104px;transform:rotate(28deg)}
  .ribbon--right{left:920px;top:192px;transform:rotate(28deg)}

  .intro{left:124px;top:480px;width:380px;font-size:8.6px;line-height:11px;color:#333}
  .intro strong{color:var(--navy);font-weight:700}
  .intro-callout{left:124px;top:539px;width:390px;font-size:9.6px;line-height:12px;color:var(--navy);font-weight:500}

  .title-band{left:548px;top:88px;width:494px;height:36px;background:var(--pink);color:#fff;
    font-weight:700;font-size:21px;letter-spacing:1.6px;display:flex;align-items:center;padding-left:40px}
  .lead{left:563px;top:135px;width:426px;text-align:center;font-size:13.2px;color:#111;font-weight:500}
  .lead-note{left:595px;top:160px;width:362px;text-align:center;font-size:10px;line-height:12px;color:var(--grey-text)}
  .tag-band{left:548px;top:533px;width:494px;height:31px;background:var(--slate);color:#fff;
    font-weight:300;font-size:14.5px;display:flex;align-items:center;padding-left:125px}
  .seal{left:616px;top:545px;width:38px;height:38px;border-radius:50%;background:#fff;border:3px solid var(--navy)}

  /* pockets */
  .pocket{position:absolute}
  .pocket--brand{width:426px;height:216px}
  .pocket--message{width:452px;height:216px}
  .flip{transform:rotate(180deg)}
  .brand-mark{position:absolute;left:128px;top:94px;display:flex;align-items:center;gap:6px}
  .brand-mark .dot{width:34px;height:34px;border-radius:50%;border:3px solid var(--navy)}
  .brand-mark span{font-weight:800;font-size:12px;line-height:12px;color:var(--navy);letter-spacing:.5px;width:80px}
  .wordmark{position:absolute;left:0;width:400px;top:148px;text-align:center;font-weight:800;font-size:19.5px;color:var(--navy)}
  .division{position:absolute;left:0;width:400px;top:174px;text-align:center;font-size:7.5px;color:#333}
  .copy{position:absolute;left:63px;top:41px;width:310px;font-size:5.6px;line-height:6.8px;color:#222}
  .copy p+p{margin-top:6px;color:#3a4a20}
  .headline{position:absolute;left:63px;top:128px;width:320px;font-family:"Rubik",sans-serif;font-weight:700;font-size:14.2px;line-height:17px;color:var(--ink)}
</style>
</head>
<body>

<svg class="dieline" viewBox="0 0 1096 1200" aria-hidden="true">
  <!-- top sheet -->
  <path d="M54 53 H1040 L1044 62 V398 A14 14 0 0 0 1044 426 V620 L1008 624 H548 H93 L54 618 V426 A14 14 0 0 0 54 398 V62 Z"
        fill="#fff" stroke="var(--die)" stroke-width="1"/>
  <line x1="547" y1="53" x2="547" y2="624" stroke="var(--fold)" stroke-dasharray="3 3" stroke-width=".8"/>
  <line x1="93" y1="624" x2="1004" y2="624" stroke="var(--fold)" stroke-dasharray="3 3" stroke-width=".8"/>
  <rect x="107" y="66" width="424" height="543" fill="none" stroke="var(--safe)" stroke-width=".8"/>
  <rect x="563" y="66" width="426" height="543" fill="none" stroke="var(--safe)" stroke-width=".8"/>

  <!-- top pockets (printed upside down) -->
  <path d="M93 624 H519 L513 800 Q510 840 470 840 H93 Z" fill="#fff" stroke="var(--die)" stroke-width="1"/>
  <path d="M123 642 H513 M123 642 V824 H470 Q505 824 508 790" fill="none" stroke="var(--safe)" stroke-width=".8"/>
  <path d="M552 624 H1004 V840 H600 Q578 840 575 815 Z" fill="var(--green)" stroke="var(--die)" stroke-width="1"/>
  <path d="M574 642 H964 V824 H600 Q590 824 588 810 Z" fill="none" stroke="var(--safe)" stroke-width=".8"/>

  <!-- bottom pockets -->
  <path d="M93 896 H500 Q528 896 532 925 L545 1112 H93 Z" fill="var(--green)" stroke="var(--die)" stroke-width="1"/>
  <path d="M133 914 H500 Q514 914 516 930 L525 1094 H133 Z" fill="none" stroke="var(--safe)" stroke-width=".8"/>
  <path d="M612 896 H1004 V1112 H579 L588 930 Q592 896 612 896 Z" fill="#fff" stroke="var(--die)" stroke-width="1"/>
  <path d="M625 914 H974 V1094 H584 M625 914 Q606 914 604 935 L600 1060" fill="none" stroke="var(--safe)" stroke-width=".8"/>
  <line x1="93" y1="1112" x2="1004" y2="1112" stroke="var(--fold)" stroke-dasharray="3 3" stroke-width=".8"/>

  <!-- card slot cut marks -->
  <g stroke="var(--die)" stroke-width=".8">
    <line x1="693" y1="976" x2="722" y2="948"/><line x1="693" y1="1018" x2="722" y2="1046"/>
    <line x1="835" y1="948" x2="864" y2="976"/><line x1="835" y1="1046" x2="864" y2="1018"/>
    <line x1="261" y1="688" x2="232" y2="716"/><line x1="261" y1="746" x2="232" y2="774"/>
    <line x1="373" y1="688" x2="402" y2="716"/><line x1="373" y1="774" x2="402" y2="746"/>
  </g>
</svg>

<!-- left cover -->
<div class="ribbon ribbon--left" role="img" aria-label="Pink and blue awareness ribbon"></div>
<div class="photo photo--beach" role="img" aria-label="Photo of a multi-generation family in white walking hand in hand on a beach"></div>
<p class="abs intro"><strong>Hereditary cancer screening</strong> provides vital information to help people with a strong personal or family history of cancer understand their own risk of developing the disease. With this information, they can take steps to Potentially Prevent Cancer, Delay the Onset of Cancer or Catch it at an Earlier stage when outcomes and survival rates are Better.</p>
<p class="abs intro-callout">Don't be Afraid of the Answer: Knowledge is Power and Power Eradicates Fear. When You are Fearless, You Will Make all the Right Choices!</p>

<!-- right cover -->
<div class="abs title-band">HEREDITARY CANCER SCREENING</div>
<p class="abs lead">Doctors are the Gatekeepers to Genetic Testing.</p>
<p class="abs lead-note">We have an obligation to help patients understand genetic risk and how testing can guide heath care decisions.</p>
<div class="ribbon ribbon--right" role="img" aria-label="Pink and blue awareness ribbon"></div>
<div class="photo photo--table" role="img" aria-label="Photo of a family sharing a meal at an outdoor table"></div>
<div class="abs tag-band">The test you order FOR your patients</div>
<div class="abs seal"></div>

<!-- pockets -->
<div class="pocket pocket--brand flip" style="left:93px;top:624px">
  <div class="brand-mark"><div class="dot"></div><span>CELVARA HEALTH GROUP</span></div>
  <div class="wordmark">Celvara Health Group</div>
  <div class="division">a division of Northvale Medical Sales LLC</div>
</div>

<div class="pocket pocket--message flip" style="left:552px;top:624px">
  <div class="copy">
    <p>There are many benefits to getting tested, regardless of the eventual result. If one of your family members — however distant — had cancer, there is a chance that you inherited a gene mutation that not only increases your personal risk of cancer, but also could be passed to the next generation. Those who are carriers of hereditary cancer gene mutations, could be at risk of getting cancer earlier in life than the general population. The sooner genetic testing is done, the more likely it is that the risk can be managed appropriately.</p>
    <p>Hereditary cancer screening provides vital information to help people with a strong personal or family history of cancer understand their own risk of developing the disease. With this information, they can take steps to Potentially Prevent Cancer, Delay the Onset of Cancer or Catch it at an Earlier stage when outcomes and survival rates are Better.</p>
  </div>
  <div class="headline">Identifying an inherited genetic mutation has the potential to prevent cancer and save lives.</div>
</div>

<div class="pocket pocket--message" style="left:93px;top:896px">
  <div class="copy">
    <p>There are many benefits to getting tested, regardless of the eventual result. If one of your family members — however distant — had cancer, there is a chance that you inherited a gene mutation that not only increases your personal risk of cancer, but also could be passed to the next generation. Those who are carriers of hereditary cancer gene mutations, could be at risk of getting cancer earlier in life than the general population. The sooner genetic testing is done, the more likely it is that the risk can be managed appropriately.</p>
    <p>Hereditary cancer screening provides vital information to help people with a strong personal or family history of cancer understand their own risk of developing the disease. With this information, they can take steps to Potentially Prevent Cancer, Delay the Onset of Cancer or Catch it at an Earlier stage when outcomes and survival rates are Better.</p>
  </div>
  <div class="headline">Identifying an inherited genetic mutation has the potential to prevent cancer and save lives.</div>
</div>

<div class="pocket pocket--brand" style="left:579px;top:896px">
  <div class="brand-mark"><div class="dot"></div><span>CELVARA HEALTH GROUP</span></div>
  <div class="wordmark">Celvara Health Group</div>
  <div class="division">a division of Northvale Medical Sales LLC</div>
</div>

</body>
</html>
```